Bluecrest Learning Corps by graduating students from college in two years

Based on the logo design, create stationary and business cards for
Dr. Venrel T Oskamp, CEO, (703) 482-1736
and Marisa Deltoft, Respresentative, (301) 647-2208
Address: 4719 Pellham Court, Brennick Falls, VA 22047
Incorporate elelments of the logo

Target Market(s)

USA

Font styles to use
Other font styles liked:
• match with the logo type style

```html
<!DOCTYPE html>
<html lang="en">
<head>
<meta charset="utf-8">
<title>Bluecrest Learning Corps — Stationery</title>
<link rel="stylesheet" href="https://fonts.googleapis.com/css2?family=Tinos:ital,wght@0,400;0,700;1,700&family=Source+Sans+3:wght@400;700&display=swap">
<style>
:root{
  --navy:#262e66;
  --yellow:#f9c532;
  --white:#ffffff;
  --stage:#d7dcdf;
  --ink:#262e66;
}
*{box-sizing:border-box;margin:0;padding:0}
html,body{width:1200px;height:916px;overflow:hidden;background:var(--stage)}
.canvas{position:relative;width:1200px;height:916px;background:linear-gradient(180deg,#dde1e3,#cfd5d9)}

.card{position:absolute;left:68px;width:437px;height:249px;overflow:hidden;box-shadow:0 6px 14px rgba(0,0,0,.35)}
.card--front{top:66px;background:var(--navy)}
.card--back{background:var(--yellow)}
.card--ceo{top:339px}
.card--rep{top:614px}

.seal{position:absolute;border-radius:50%;display:flex;align-items:center;justify-content:center;text-align:center;font-family:"Tinos",serif;font-weight:700;line-height:1.15}
.seal--front{left:147px;top:54px;width:142px;height:142px;background:var(--yellow);color:var(--navy);font-size:15px}
.seal--back{left:-1px;top:-1px;width:250px;height:250px;background:var(--white);border:6px solid var(--navy);color:var(--navy);font-size:24px}

.card__bar{position:absolute;left:425px;top:27px;width:12px;height:28px;background:var(--white)}
.card__text{position:absolute;right:16px;text-align:right;color:var(--white);font-family:"Tinos",serif;white-space:nowrap}
.card__name{top:22px;font-size:18.5px;font-weight:700;letter-spacing:.3px}
.card__role{top:44px;font-size:11px}
.card__address{top:135px;font-size:11px;line-height:14.5px}
.card__contacts{top:187px;font-size:11px;line-height:14.8px}
.card__contacts li{list-style:none;display:flex;align-items:center;justify-content:flex-end;gap:5px}
.icon{width:10px;height:10px;flex:none}

.letter{position:absolute;left:563px;top:66px;width:558px;height:787px;background:var(--white);box-shadow:0 8px 18px rgba(0,0,0,.3);color:var(--ink)}
.letter__seal{position:absolute;left:243px;top:28px;width:66px;height:66px;border-radius:50%;background:var(--yellow);border:3px solid var(--navy);display:flex;align-items:center;justify-content:center;text-align:center;font-family:"Source Sans 3",sans-serif;font-weight:700;font-size:8.5px;line-height:1.1;color:var(--navy)}
.letter__block{position:absolute;left:31px;font-family:"Source Sans 3",sans-serif}
.letter__date{top:167px;font-size:11px}
.letter__to{top:191px;font-size:11px;line-height:12.5px}
.letter__to strong{display:block;font-size:15px;line-height:16px}
.letter__addr{top:229px;font-size:11px;line-height:14px}
.letter__salute{top:280px;font-size:15px;font-weight:700}
.letter__body{top:309px;width:498px;font-size:11.6px;line-height:14.6px;text-align:justify}
.letter__body p+p{margin-top:14.4px}
.letter__signature{position:absolute;left:31px;top:562px;width:150px;height:36px;background:linear-gradient(90deg,rgba(38,46,102,.18),rgba(38,46,102,.05))}
.letter__sender{top:597px;font-size:26px;font-weight:700;line-height:28px}
.letter__sender span{display:block;font-size:11px;font-weight:400;line-height:13px}

.letter__footer{position:absolute;left:0;bottom:0;width:558px;height:58px;background:var(--yellow);color:var(--white);font-family:"Tinos",serif;font-size:12px;line-height:16px}
.letter__footer-seal{position:absolute;left:1px;top:1px;width:56px;height:56px;border-radius:50%;background:var(--white);border:3px solid var(--navy);display:flex;align-items:center;justify-content:center;text-align:center;font-family:"Tinos",serif;font-weight:700;font-size:7px;line-height:1.1;color:var(--navy)}
.footer__col{position:absolute;top:13px}
.footer__col li{list-style:none;display:flex;align-items:center;gap:6px}
.footer__web{left:110px}
.footer__place{left:355px;display:flex;gap:6px}

.label{position:absolute;font-family:"Tinos",serif;font-style:italic;font-weight:700;font-size:30px;color:#f3f4f5;text-shadow:0 2px 3px rgba(0,0,0,.35);letter-spacing:1px}
.label--cards{left:143px;top:870px}
.label--letter{left:728px;top:862px}
</style>
</head>
<body>
<main class="canvas">

  <section class="card card--front" aria-label="Business card front">
    <div class="seal seal--front">Bluecrest<br>Learning<br>Corps</div>
  </section>

  <section class="card card--back card--ceo" aria-label="Business card, CEO">
    <div class="seal seal--back">Bluecrest<br>Learning<br>Corps</div>
    <div class="card__bar"></div>
    <div class="card__text card__name">Dr. Venrel T Oskamp</div>
    <div class="card__text card__role">CEO</div>
    <div class="card__text card__address">4719 Pellham Court,<br>Brennick Falls, VA 22047</div>
    <ul class="card__text card__contacts">
      <li>(703) 482-1736 <svg class="icon" viewBox="0 0 10 10"><circle cx="5" cy="5" r="5" fill="#fff"/><path d="M3 2.5l1 1-.6.8c.4.9 1 1.5 1.9 1.9l.8-.6 1 1-.8.9C4.8 7.3 2.7 5.2 2.5 3.3z" fill="#f9c532"/></svg></li>
      <li>www.yourwebsite.com <svg class="icon" viewBox="0 0 10 10"><circle cx="5" cy="5" r="5" fill="#fff"/><path d="M1 5h8M5 1v8M5 1c-2 2-2 6 0 8M5 1c2 2 2 6 0 8" stroke="#f9c532" stroke-width=".7" fill="none"/></svg></li>
      <li>info@yourwebsite.com <svg class="icon" viewBox="0 0 10 10"><rect width="10" height="10" rx="2" fill="#fff"/><path d="M2 3.2h6v4H2zM2 3.2l3 2.4 3-2.4" stroke="#f9c532" stroke-width=".7" fill="none"/></svg></li>
    </ul>
  </section>

  <section class="card card--back card--rep" aria-label="Business card, representative">
    <div class="seal seal--back">Bluecrest<br>Learning<br>Corps</div>
    <div class="card__bar"></div>
    <div class="card__text card__name">Marisa Deltoft</div>
    <div class="card__text card__role">Respresentative</div>
    <div class="card__text card__address">4719 Pellham Court,<br>Brennick Falls, VA 22047</div>
    <ul class="card__text card__contacts">
      <li>(301) 647-2208 <svg class="icon" viewBox="0 0 10 10"><circle cx="5" cy="5" r="5" fill="#fff"/><path d="M3 2.5l1 1-.6.8c.4.9 1 1.5 1.9 1.9l.8-.6 1 1-.8.9C4.8 7.3 2.7 5.2 2.5 3.3z" fill="#f9c532"/></svg></li>
      <li>www.yourwebsite.com <svg class="icon" viewBox="0 0 10 10"><circle cx="5" cy="5" r="5" fill="#fff"/><path d="M1 5h8M5 1v8M5 1c-2 2-2 6 0 8M5 1c2 2 2 6 0 8" stroke="#f9c532" stroke-width=".7" fill="none"/></svg></li>
      <li>info@yourwebsite.com <svg class="icon" viewBox="0 0 10 10"><rect width="10" height="10" rx="2" fill="#fff"/><path d="M2 3.2h6v4H2zM2 3.2l3 2.4 3-2.4" stroke="#f9c532" stroke-width=".7" fill="none"/></svg></li>
    </ul>
  </section>

  <article class="letter" aria-label="A4 letterhead">
    <div class="letter__seal">Bluecrest<br>Learning<br>Corps</div>
    <div class="letter__block letter__date">August-05-2019</div>
    <div class="letter__block letter__to"><strong>Helena Vastrow</strong>Director</div>
    <div class="letter__block letter__addr">1380 Thornfield Ave. Suite 200<br>Halden Ridge, TX 76354</div>
    <div class="letter__block letter__salute">Helena Vastrow</div>
    <div class="letter__block letter__body">
      <p>Lorem ipsum dolor sit amet, consectetuer adipiscing elit, sed diam nonummy nibh euismod tincidunt ut laoreet dolore magna aliquam erat volutpat. Ut wisi enim ad minim veniam, quis nostrud exerci tation ullamcorper suscipit lobortis</p>
      <p>Lorem ipsum dolor sit amet, cons ectetuer adipiscing elit, sed diam nonummy nibh euismod tincidunt ut laoreet dolore magna aliquam erat volutpat. Ut wisi enim ad minim veniam, quis nostrud exerci tation ullamcorper suscipit lobortis nisl ut aliquip ex ea commodo consequat. Lorem ipsum dolor sit amet, consectetuer olutpat. Ut wisi enim ad minim veniam, quis nostrud exerci tation ullamcorper suscipit lobortis nisl ut aliquip ex ea commodo consequat. Duis autem</p>
      <p>vel eum iriure dolor in hendrerit in vulputate velit esse molestie consequat, vel illum dolore eu feugiat nulla facilisis at vero eros et accumsan et iusto odio dignissim qui blandit praesent luptatum zzril delenit augue duis dolore te feugait nulla facilisi. Lorem ipsum dolor sit amet, cons ectetuer adipiscing elit, sed diam nonummy nibh euismod tincidunt ut laoreet dolore magna aliquam erat volutpat. Ut wisi enim .</p>
    </div>
    <div class="letter__signature" role="img" aria-label="Handwritten signature of the sender"></div>
    <div class="letter__block letter__sender">Jonah Perrel<span>Co-Founder</span></div>

    <footer class="letter__footer">
      <div class="letter__footer-seal">Bluecrest<br>Learning<br>Corps</div>
      <ul class="footer__col footer__web">
        <li><svg class="icon" viewBox="0 0 10 10"><circle cx="5" cy="5" r="5" fill="#fff"/><path d="M1 5h8M5 1v8M5 1c-2 2-2 6 0 8M5 1c2 2 2 6 0 8" stroke="#f9c532" stroke-width=".7" fill="none"/></svg>info@yourwebsite.com</li>
        <li><svg class="icon" viewBox="0 0 10 10"><rect width="10" height="10" rx="2" fill="#fff"/><path d="M2 3.2h6v4H2zM2 3.2l3 2.4 3-2.4" stroke="#f9c532" stroke-width=".7" fill="none"/></svg>www.yourwebsite.com</li>
      </ul>
      <div class="footer__col footer__place">
        <svg width="11" height="16" viewBox="0 0 11 16"><path d="M5.5 1A4.2 4.2 0 0 0 1.3 5.2c0 3.2 4.2 8.3 4.2 8.3s4.2-5.1 4.2-8.3A4.2 4.2 0 0 0 5.5 1z" fill="none" stroke="#fff" stroke-width="1.2"/><circle cx="5.5" cy="5.2" r="1.5" fill="#fff"/><path d="M2 15h7" stroke="#fff" stroke-width="1"/></svg>
        <span>4719 Pellham Court,<br>Brennick Falls, VA 22047</span>
      </div>
    </footer>
  </article>

  <div class="label label--cards">Business card</div>
  <div class="label label--letter">A4 Letterhead</div>

</main>
</body>
</html>
```